Heron Dusk business card design

I make handmade colourful women's beaded jewellery (necklaces and earnings).
I require a business card to be designed to truly reflect my jewellery, that is, it is different and stands out.
I would like the business card to look creative, arty, gentle and feminine and fit in with the look of my website and logo (already developed).
I would like the business card to have strong use of the water reeds that are flowing in the wind (please see the banner image on my website www.herondusk.net and attached files).

Target Market(s)

Women who are fashion conscious, hip and funky. My audience like things that are a little different and stand out in a crowd.These women are aged in their 20's-40's.

Industry/Entity Type

Jewelry

Contact Information for Business Card

Please include the following items:
1) my logo: Heron Dusk
2) my name, address and phone number: Darla Fontenot, Sydney, Australia, 0498 315 270
3) my web details: www.herondusk.net, info@herondusk.net, www.socialcove.com/herondusk

Font styles to use
Other font styles liked:
• Remachine Script

Requirements
Must have
• My business card must have the following:
• 1) my personal details including all my website contacts (see above).
• 2) Heron Dusk logo
• 3) Reeds flowing in the wind (see my banner image on my website www.herondusk.net or see attached files).
Nice to have
• A sunrise in the background (rising over water)
• I would prefer that the colour scheme to fit with the Heron Dusk logo, that is the colours of an early morning sunrise i.e yellows, oranges. The use of black and white is fine.
Should not have
• I do not like a commercial manufactured look with hard edges. I would like a look that is soft and reflects an artistic, creative and independent business.

```html
<!DOCTYPE html>
<html lang="en">
<head>
<meta charset="utf-8">
<title>Heron Dusk – Business Card</title>
<link rel="stylesheet" href="https://fonts.googleapis.com/css2?family=Source+Sans+3:wght@400;600&display=swap">
<style>
  :root {
    --paper: #ffffff;
    --ink: #1c1c1c;
    --sun-orange: #f39200;
    --sun-yellow: #f7b21a;
    --reed-light: #f3f3f3;
    --reed-mid: #cdcdcd;
    --reed-dark: #a3a3a3;
  }
  * { box-sizing: border-box; margin: 0; padding: 0; }
  html, body { width: 693px; height: 1200px; overflow: hidden; background: var(--paper); }
  .card {
    position: relative;
    width: 693px;
    height: 1200px;
    overflow: hidden;
    background: var(--paper);
    font-family: "Source Sans 3", "Myriad Pro", Arial, sans-serif;
    color: var(--ink);
  }
  .reed-field {
    position: absolute;
    left: 0; right: 0; top: 400px; bottom: 0;
    background:
      linear-gradient(180deg, rgba(255,255,255,1) 0%, rgba(255,255,255,0) 35%),
      linear-gradient(180deg, var(--reed-light) 20%, var(--reed-mid) 70%, var(--reed-dark) 100%);
  }
  .brand-name {
    position: absolute;
    left: 0; right: 0; top: 52px;
    text-align: center;
    font-size: 56px;
    font-weight: 600;
    line-height: 1;
    letter-spacing: 1px;
    color: var(--ink);
  }
  .brand-disc {
    position: absolute;
    left: 175px; top: 140px;
    width: 372px; height: 372px;
    border-radius: 50%;
    border: 7px solid var(--ink);
    background: var(--sun-yellow);
  }
  .person {
    position: absolute;
    left: 0; right: 0; top: 578px;
    text-align: center;
  }
  .person-name {
    font-size: 42px;
    font-weight: 600;
    color: var(--sun-orange);
    line-height: 1.1;
  }
  .person-role {
    margin-top: 12px;
    font-size: 30px;
    font-weight: 600;
    color: var(--ink);
  }
  .contacts {
    position: absolute;
    left: 0; right: 0; top: 842px;
    list-style: none;
    text-align: center;
  }
  .contact {
    font-size: 32px;
    font-weight: 600;
    line-height: 52px;
    white-space: nowrap;
  }
  .contact-icon {
    display: inline-block;
    width: 26px; height: 26px;
    margin-right: 10px;
    vertical-align: -3px;
  }
  .location {
    position: absolute;
    left: 0; right: 0; top: 1090px;
    text-align: center;
    font-size: 32px;
    font-weight: 600;
  }
</style>
</head>
<body>
<div class="card">
  <div class="reed-field" role="img" aria-label="Grey reeds and bulrushes swaying in the wind"></div>

  <div class="brand-name">Heron Dusk</div>
  <span class="brand-disc"></span>

  <div class="person">
    <div class="person-name">Darla Fontenot</div>
    <div class="person-role">Owner</div>
  </div>

  <ul class="contacts">
    <li class="contact">
      <svg class="contact-icon" viewBox="0 0 24 24" aria-hidden="true">
        <path fill="#f39200" d="M6.6 10.8a15.1 15.1 0 0 0 6.6 6.6l2.2-2.2a1 1 0 0 1 1-.25 11.4 11.4 0 0 0 3.6.57 1 1 0 0 1 1 1V20a1 1 0 0 1-1 1A17 17 0 0 1 3 4a1 1 0 0 1 1-1h3.5a1 1 0 0 1 1 1c0 1.25.2 2.45.57 3.6a1 1 0 0 1-.25 1z"/>
      </svg>0498 315 270
    </li>
    <li class="contact">
      <svg class="contact-icon" viewBox="0 0 24 24" aria-hidden="true">
        <rect x="1" y="5" width="22" height="14" fill="#f39200"/>
        <path d="M1 5l11 8 11-8M1 19l8-7M23 19l-8-7" stroke="#fff" stroke-width="1.5" fill="none"/>
      </svg>info@herondusk.net
    </li>
    <li class="contact">
      <svg class="contact-icon" viewBox="0 0 24 24" aria-hidden="true">
        <g fill="none" stroke="#f7b21a" stroke-width="2.6" stroke-linecap="round">
          <path d="M10 14a4 4 0 0 0 5.7 0l3.6-3.6a4 4 0 0 0-5.7-5.7l-1.3 1.3"/>
          <path d="M14 10a4 4 0 0 0-5.7 0l-3.6 3.6a4 4 0 0 0 5.7 5.7l1.3-1.3"/>
        </g>
      </svg>www.herondusk.net
    </li>
    <li class="contact">
      <svg class="contact-icon" viewBox="0 0 24 24" aria-hidden="true">
        <circle cx="12" cy="12" r="9" fill="#f39200"/>
      </svg>www.socialcove.com/herondusk
    </li>
  </ul>

  <div class="location">Sydney, Australia</div>
</div>
</body>
</html>
```